Global (re)insurance broker needs a business card design

We need a classic business card for our company that is headquartered in SG, with offices in Malaysia and Dubai. We specialise in insurance and reinsurance broking and consultancy for our global clients.

```html
<!DOCTYPE html>
<html lang="en">
<head>
<meta charset="utf-8">
<title>Halvex – Business Card</title>
<link href="https://fonts.googleapis.com/css2?family=Open+Sans:wght@400;600;700&display=swap" rel="stylesheet">
<style>
  :root {
    --backdrop: #232323;
    --card: #1f1f24;
    --card-back: #1d1d22;
    --mark-dark: #0e0e10;
    --brand-blue: #2a4ea6;
    --brand-green: #c3dfb8;
    --ink-light: #ffffff;
    --rule: #8a8a90;
  }
  * { margin: 0; padding: 0; box-sizing: border-box; }
  html, body {
    width: 1200px; height: 780px; overflow: hidden;
    background: var(--backdrop);
    font-family: "Open Sans", Arial, sans-serif;
  }
  .canvas {
    position: relative; width: 1200px; height: 780px;
    display: flex; align-items: center; justify-content: center; gap: 40px;
  }
  .card {
    position: relative; width: 540px; height: 309px;
    box-shadow: 0 10px 30px rgba(0,0,0,.55);
    overflow: hidden;
  }
  .card--back { background: var(--card-back); display: flex; align-items: center; justify-content: center; }
  .card--back .wordmark { color: var(--mark-dark); font-size: 72px; }
  .card--front { background: var(--card); }
  .wordmark {
    font-weight: 700; letter-spacing: 2px; line-height: 1;
  }
  .card--front .wordmark {
    position: absolute; left: 0; right: 0; top: 52px; text-align: center;
    color: var(--brand-green); font-size: 64px;
  }
  .person { position: absolute; left: 52px; top: 180px; }
  .person__name { font-size: 30px; font-weight: 700; line-height: 1.1; }
  .person__first { color: var(--brand-blue); }
  .person__last { color: var(--brand-green); }
  .person__title { color: var(--ink-light); font-size: 14px; font-weight: 600; margin-top: 2px; }
  .divider {
    position: absolute; left: 300px; top: 166px; width: 1px; height: 80px;
    background: var(--rule);
  }
  .contacts {
    position: absolute; left: 318px; top: 168px; list-style: none;
    color: var(--ink-light); font-size: 13px;
  }
  .contacts li { display: flex; align-items: center; gap: 8px; height: 24px; }
  .contacts svg { width: 14px; height: 14px; flex: none; }
  .address-band {
    position: absolute; left: 0; right: 0; bottom: 22px; height: 26px;
    background: var(--brand-blue); color: var(--ink-light);
    font-size: 13px; display: flex; align-items: center; justify-content: center;
  }
</style>
</head>
<body>
<main class="canvas">
  <section class="card card--back" aria-label="Card back">
    <span class="wordmark">HALVEX</span>
  </section>

  <section class="card card--front" aria-label="Card front">
    <span class="wordmark">HALVEX</span>

    <div class="person">
      <p class="person__name"><span class="person__first">Lena</span> <span class="person__last">Ortiz</span></p>
      <p class="person__title">Chief Operating Officer</p>
    </div>

    <div class="divider"></div>

    <ul class="contacts">
      <li>
        <svg viewBox="0 0 14 14" aria-hidden="true"><rect x="3.5" y="1" width="7" height="12" rx="1.2" fill="none" stroke="#fff" stroke-width="1"/></svg>
        +65 5550 2846
      </li>
      <li>
        <svg viewBox="0 0 14 14" aria-hidden="true"><circle cx="7" cy="7" r="6" fill="var(--brand-blue)"/><path d="M1 7h12M7 1c-2.5 3-2.5 9 0 12M7 1c2.5 3 2.5 9 0 12" fill="none" stroke="#1f1f24" stroke-width=".8"/></svg>
        www.halvex.com
      </li>
      <li>
        <svg viewBox="0 0 14 14" aria-hidden="true"><rect x="1" y="3" width="12" height="8.5" fill="none" stroke="var(--brand-green)" stroke-width="1"/><path d="M1 3l6 5 6-5" fill="none" stroke="var(--brand-green)" stroke-width="1"/></svg>
        lena@halvex.com
      </li>
    </ul>

    <div class="address-band">28 Kellner Quay, Harbourline Tower #08-04, Singapore 000000</div>
  </section>
</main>
</body>
</html>
```